Hvac and insulation company needs good looking business card design

We are hvac and insulation company and looking for a new business cards that look to today standards designs

Target Market(s)

homeowners

Industry/Entity Type

Hvac

Contact Information for Business Card

Name: Walter Brinoku
Home comfort consultant
address: 4827 Dunmore St #215 Oakland, CA 94619
office: 888-316-2790
cell: 510-742-3185
Lic.# 584261
Email: walter@corvane-hvac.com
Web: corvane-hvac.com

Requirements
Must have
• clean and sleek look
Nice to have
• simple with a clean look
Should not have
• to busy business card

```html
<!DOCTYPE html>
<html lang="en">
<head>
<meta charset="utf-8">
<title>Corvane Home Solutions – Business Card</title>
<link href="https://fonts.googleapis.com/css2?family=Questrial&family=Oswald:wght@500;600&display=swap" rel="stylesheet">
<style>
  :root {
    --orange: #f7901e;
    --black: #161616;
    --white: #f7f7f7;
    --grey-text: #6e6e6e;
    --grey-soft: #9a9a9a;
    --grey-band: #a9a9a9;
    --stage: #2b2b2b;
  }
  * { box-sizing: border-box; margin: 0; padding: 0; }
  html, body {
    width: 1200px; height: 886px; overflow: hidden;
    background: var(--stage);
    font-family: "Questrial", sans-serif;
  }
  .canvas { position: relative; width: 1200px; height: 886px; }

  .card {
    position: absolute;
    width: 620px; height: 354px;
    border-radius: 22px;
    overflow: hidden;
  }

  /* Back side */
  .card--back { left: 70px; top: 70px; background: var(--black); }
  .social {
    position: absolute; top: 22px; right: 26px;
    display: flex; gap: 5px;
  }
  .social__dot { width: 20px; height: 20px; border-radius: 50%; background: var(--orange); }
  .brand { position: absolute; display: flex; align-items: center; gap: 14px; }
  .brand__mark { background: var(--orange); border-radius: 6px; }
  .brand__name {
    color: var(--orange); line-height: 1;
    font-family: "Questrial", sans-serif;
  }
  .brand__tag {
    color: var(--grey-soft); letter-spacing: 0.18em; line-height: 1;
  }
  .card--back .brand { left: 150px; top: 120px; }
  .card--back .brand__mark { width: 58px; height: 58px; }
  .card--back .brand__name { font-size: 64px; }
  .card--back .brand__tag { font-size: 17px; margin: 4px 0 0 26px; }
  .back__web {
    position: absolute; left: 0; right: 0; bottom: 56px;
    text-align: center; color: #fff; font-size: 15px; letter-spacing: 0.42em;
  }

  /* Front side */
  .card--front { left: 520px; top: 466px; background: var(--white); }
  .card--front .brand { left: 42px; top: 150px; }
  .card--front .brand__mark { width: 44px; height: 44px; }
  .card--front .brand__name { font-size: 50px; }
  .card--front .brand__tag { font-size: 13px; margin: 3px 0 0 20px; }
  .divider {
    position: absolute; left: 316px; top: 58px;
    width: 1px; height: 200px; background: #cfcfcf;
  }
  .contact { position: absolute; left: 340px; top: 56px; color: var(--grey-text); }
  .contact__name {
    font-family: "Oswald", sans-serif; font-weight: 600;
    color: var(--orange); font-size: 22px; text-transform: uppercase; line-height: 1.1;
  }
  .contact__role {
    font-family: "Oswald", sans-serif; font-weight: 500;
    font-size: 15px; text-transform: uppercase; letter-spacing: 0.02em; margin-bottom: 14px;
  }
  .contact__address { font-size: 14px; line-height: 1.35; margin-bottom: 12px; }
  .contact__line { display: flex; align-items: center; gap: 8px; font-size: 14px; line-height: 1.5; }
  .contact__line svg { width: 12px; height: 12px; fill: var(--orange); flex: none; }
  .front__band { position: absolute; left: 0; bottom: 0; width: 620px; height: 74px; }
  .front__web {
    position: absolute; right: 26px; bottom: 18px;
    color: #fff; font-size: 15px; letter-spacing: 0.3em;
  }
</style>
</head>
<body>
<main class="canvas">

  <section class="card card--back" aria-label="Card back">
    <div class="social" aria-label="Social links">
      <span class="social__dot"></span><span class="social__dot"></span><span class="social__dot"></span>
    </div>
    <div class="brand">
      <span class="brand__mark"></span>
      <div>
        <div class="brand__name">corvane</div>
        <div class="brand__tag">home solutions</div>
      </div>
    </div>
    <p class="back__web">www.corvane-hvac.com</p>
  </section>

  <section class="card card--front" aria-label="Card front">
    <div class="brand">
      <span class="brand__mark"></span>
      <div>
        <div class="brand__name">corvane</div>
        <div class="brand__tag">home solutions</div>
      </div>
    </div>
    <span class="divider"></span>
    <div class="contact">
      <h1 class="contact__name">Walter Brinoku</h1>
      <p class="contact__role">Home Comfort Consultant</p>
      <p class="contact__address">4827 Dunmore St #215<br>Oakland, CA 94619</p>
      <p class="contact__line">
        <svg viewBox="0 0 12 12" aria-hidden="true"><path d="M2 1l2.2 0 1 2.6-1.3 1a6 6 0 0 0 3.5 3.5l1-1.3L11 7.8V10c0 .6-.4 1-1 1A9 9 0 0 1 1 2c0-.6.4-1 1-1z"/></svg>
        888-316-2790</p>
      <p class="contact__line">
        <svg viewBox="0 0 12 12" aria-hidden="true"><path d="M3 0h6a1 1 0 0 1 1 1v10a1 1 0 0 1-1 1H3a1 1 0 0 1-1-1V1a1 1 0 0 1 1-1zm.5 1.5v7.5h5V1.5z"/></svg>
        510-742-3185</p>
      <p class="contact__line">
        <svg viewBox="0 0 12 12" aria-hidden="true"><path d="M0 2h12v1.2L6 7 0 3.2zM0 4.6l6 3.8 6-3.8V10H0z"/></svg>
        walter@corvane-hvac.com</p>
    </div>
    <svg class="front__band" viewBox="0 0 620 74" aria-hidden="true">
      <polygon points="0,54 366,54 374,44 390,44 390,64 0,64" fill="var(--grey-band)"/>
      <polygon points="0,64 390,64 398,54 412,10 620,10 620,74 0,74" fill="var(--orange)"/>
    </svg>
    <p class="front__web">corvane-hvac.com</p>
  </section>

</main>
</body>
</html>
```